KAJU Freightways #ALLKAJU Business Cards & Letterhead

I am looking to business cards designed for our organization. We are currently undergoing a small re-branding that is taking place. Our organization is called KAJU Freightways and we are headquartered in Phoenix, AZ. We primarily provide transportation and logistics services to the Marlow Parcel Bureau who is our largest customer. I would like to see a design that incorporates name, title, contact info, website, and address (this will be different depending on the employee). I would also like to see some color on the business card using our logo colors or a variation. I would like our logo on the back of the business card with the website displayed. The final design should communicate that we are a next generation transportation operate that focuses on being driver-first, customer-centric, innovative, and sustainable.We would also like our #ALLKAJU catch phrase incorporated as well.

Target Market(s)

Transportation & Logistics

Industry/Entity Type

Trucking Company

Contact Information for Business Card

-First and Last Name
-Position Title
-Contact Phone
-Contact Email
-Physical Address

Font styles to use
Serif

Colors

Designer to choose colors to be used in the design.

Requirements
Must have
• -KAJU logo prominently displayed
• -#ALLKAJU catch phrase used
• -Some amount of color, design gradient, etc.
• -Logo on the back with website listed (https://www.kajufreightco.example)

```html
<!DOCTYPE html>
<html lang="en">
<head>
<meta charset="utf-8">
<title>KAJU Freightways – Letterhead &amp; Business Cards</title>
<link href="https://fonts.googleapis.com/css2?family=Lato:wght@400;700&family=Arimo:wght@400;700&display=swap" rel="stylesheet">
<style>
  :root{
    --teal:#153a44;
    --green:#7aba42;
    --paper:#f5f5f5;
    --ink:#1c1c1c;
    --stage:#e3e3e3;
    --shadow:0 3px 6px rgba(0,0,0,.35);
  }
  *{box-sizing:border-box;margin:0;padding:0}
  html,body{width:1200px;height:1200px;overflow:hidden}
  body{background:radial-gradient(circle at 55% 50%,#f0f0f0 0%,var(--stage) 70%);font-family:"Lato",sans-serif;position:relative}

  /* ---------- Letterhead ---------- */
  .letterhead{position:absolute;left:86px;top:155px;width:703px;height:908px;background:var(--paper);box-shadow:var(--shadow);overflow:hidden}
  .letterhead .shapes{position:absolute;inset:0;width:100%;height:100%}
  .brand{position:absolute;display:flex;align-items:center;gap:6px;color:#fff;font-family:"Lato",sans-serif;font-weight:700}
  .letterhead .brand{left:42px;top:52px;font-size:28px;letter-spacing:1px}
  .brand-dot{border-radius:50%;background:var(--green);flex:none}
  .letterhead .brand-dot{width:12px;height:12px}
  .divider{position:absolute;background:#fff;width:1px}
  .letterhead .divider{left:143px;top:30px;height:76px}
  .tagline{position:absolute;color:var(--green);font-family:"Lato",sans-serif;line-height:1.2}
  .letterhead .tagline{left:155px;top:51px;font-size:13.5px}
  .sender{position:absolute;right:55px;top:57px;text-align:right;color:var(--teal);font-size:10.2px;line-height:12.6px}
  .sender .company{font-weight:700}
  .sender .contacts{margin-top:6px}
  .contact-line{display:flex;justify-content:flex-end;align-items:center;gap:4px}
  .icon{width:8px;height:8px;flex:none}
  .letter{position:absolute;left:55px;top:231px;width:594px;font-family:"Arimo",sans-serif;font-size:9.6px;line-height:13.7px;color:var(--ink)}
  .letter .recipient{margin-top:14px}
  .letter .salutation{margin-top:29px;font-weight:700}
  .letter .body{margin-top:28px}
  .letter .body p{text-align:justify;margin-bottom:13.7px}
  .letter .closing{margin-top:27px}
  .signature{display:block;width:140px;height:22px;margin-top:18px;border-radius:3px;background:linear-gradient(90deg,rgba(28,28,28,.18),rgba(28,28,28,.06))}
  .signer{margin-top:11px}
  .hashtag{position:absolute;color:#fff;font-family:"Lato",sans-serif}
  .hashtag span{color:var(--green)}
  .letterhead .hashtag{right:67px;top:871px;font-size:12px}
  .faint-name{position:absolute;font-family:"Lato",sans-serif;font-weight:700;color:rgba(255,255,255,.06)}
  .letterhead .faint-name{right:30px;top:848px;font-size:52px}

  /* ---------- Business cards ---------- */
  .card{position:absolute;left:839px;width:289px;height:165px;box-shadow:var(--shadow);overflow:hidden}
  .card-back{top:283px;background:var(--teal)}
  .card-back .brand{left:34px;top:70px;font-size:22px;letter-spacing:1px}
  .card-back .brand-dot{width:9px;height:9px}
  .card-back .divider{left:128px;top:53px;height:58px}
  .card-back .tagline{left:138px;top:71px;font-size:9.6px}
  .card-back .website{position:absolute;left:0;right:0;top:138px;text-align:center;color:#fff;font-size:7px;letter-spacing:1.3px}
  .card-back .website span{color:var(--green)}

  .card-front{top:473px;background:var(--paper)}
  .card-front .shapes{position:absolute;inset:0;width:100%;height:100%}
  .card-front .brand{left:16px;top:14px;font-size:17px;letter-spacing:.5px}
  .card-front .brand-dot{width:7px;height:7px}
  .holder{position:absolute;right:21px;top:44px;text-align:right}
  .holder .name{color:var(--green);font-size:10.5px}
  .holder .title{color:var(--teal);font-size:7px;margin-top:1px}
  .card-details{position:absolute;left:20px;top:80px;color:var(--teal);font-size:6.8px;line-height:9.6px}
  .card-details .company{font-weight:700}
  .card-details .contacts{margin-top:3px}
  .card-details .contact-line{justify-content:flex-start;gap:3px}
  .card-details .icon{width:6px;height:6px}
  .card-details .green{color:var(--green)}
  .card-front .hashtag{right:24px;top:147px;font-size:8px}
  .card-front .faint-name{right:4px;top:136px;font-size:26px}
</style>
</head>
<body>

<!-- Letterhead -->
<section class="letterhead">
  <svg class="shapes" viewBox="0 0 1132 1463" preserveAspectRatio="none" aria-hidden="true">
    <path fill="var(--teal)" d="M0 0H1132V45C950 20 800 50 600 120C400 190 250 225 150 215C80 208 30 195 0 185Z"/>
    <path fill="var(--green)" d="M0 185C30 195 80 208 150 215C250 225 400 190 600 120C800 50 950 20 1132 45V82C950 40 800 70 600 140C400 210 250 235 150 225C80 220 30 208 0 195Z"/>
    <path fill="var(--green)" d="M510 1463C750 1420 950 1340 1100 1230C1000 1330 820 1420 660 1463Z"/>
    <path fill="var(--teal)" d="M660 1463C850 1420 1020 1330 1132 1200V1463Z"/>
  </svg>

  <div class="brand"><span class="brand-dot"></span>KAJU</div>
  <span class="divider"></span>
  <p class="tagline">Transportation<br>and Energy Services</p>

  <address class="sender" style="font-style:normal">
    <div class="company">KAJU Freightways &amp; Energy Services, Inc.</div>
    <div>4410 North Cactus Ridge Road</div>
    <div>Phoenix, AZ 85016</div>
    <div class="contacts">
      <div class="contact-line">602-555-0148
        <svg class="icon" viewBox="0 0 10 10"><path fill="var(--green)" d="M2 0.5L3.6 2.6 2.8 3.8C3.4 5 4.8 6.5 6.2 7.2L7.4 6.4 9.5 8 8.4 9.6C4.5 9.3 0.8 5.5 0.4 1.6Z"/></svg>
      </div>
      <div class="contact-line">info@kajufreightco.example
        <svg class="icon" viewBox="0 0 10 10"><rect x="0.6" y="1.8" width="8.8" height="6.4" fill="none" stroke="var(--green)" stroke-width="1"/><path d="M0.8 2l4.2 3.4L9.2 2" fill="none" stroke="var(--green)" stroke-width="1"/></svg>
      </div>
      <div class="contact-line">www.kajufreightco.example
        <svg class="icon" viewBox="0 0 10 10"><circle cx="5" cy="5" r="4.3" fill="none" stroke="var(--green)" stroke-width="0.9"/><ellipse cx="5" cy="5" rx="1.8" ry="4.3" fill="none" stroke="var(--green)" stroke-width="0.8"/><path d="M0.8 5h8.4M1.5 3h7M1.5 7h7" stroke="var(--green)" stroke-width="0.7"/></svg>
      </div>
    </div>
  </address>

  <article class="letter">
    <p class="date">November 15, 2019</p>
    <p class="recipient">Mr. John Doe<br>President<br>AA Corporation<br>111 Street Name, Suite#<br>City, State, 12345</p>
    <p class="salutation">Dear Mr. John,</p>
    <div class="body">
      <p>Lorem ipsum dolor sit amet, consectetur adipiscing elit. Integer diam quam, egestas eu ultrices eu, suscipit ac sapien. Phasellus eu dui nisi. Nam et euismod diam, nec lobortis tortor. Donec et diam nulla. Aenean varius tincidunt convallis. Aliquam a tortor at lacus dictum aliquet. Nunc laoreet metus sapien, in scelerisque augue consectetur in.</p>
      <p>Fusce nec justo laoreet, egestas justo sed, aliquet sem. Pellentesque pharetra massa non orci bibendum semper. Pellentesque cursus eu lectus a consectetur. Nunc volutpat suscipit posuere. Vestibulum facilisis vel quam malesuada mattis. Nulla in mattis tellus. Maecenas tristique mauris vitae pharetra tincidunt. In ut ornare risus. Integer molestie vestibulum nisi, semper dapibus mi condimentum eu.</p>
      <p>Nullam sagittis elit libero, id fringilla est tincidunt eget. Donec in ipsum ultricies, consectetur quam vel, facilisis elit. Phasellus tincidunt congue risus vel luctus. Suspendisse ut mollis neque. Donec ornare orci in turpis vestibulum, in ultrices metus scelerisque. Pellentesque mattis mattis nunc, nec tincidunt lacus egestas id. Fusce facilisis sagittis neque sit amet vulputate. Aliquam ut eros lobortis tortor facilisis vehicula. Sed sed luctus leo, at laoreet sapien. Donec placerat adipiscing ligula non euismod. In lobortis pretium nisl id luctus.</p>
      <p>Integer gravida tincidunt nibh, scelerisque tincidunt turpis. Suspendisse potenti. Nunc hendrerit euismod lectus id elementum. Fusce vitae gravida velit, quis eleifend lectus. In imperdiet mauris eu dui viverra sagittis. Donec tempor dui diam, condimentum gravida lacus pretium a. Nullam fringilla augue quis arcu placerat scelerisque. Aliquam nec tincidunt augue, sit amet posuere ipsum.</p>
    </div>
    <p class="closing">Sincerely Yours,</p>
    <span class="signature" role="img" aria-label="Handwritten signature of Dana Whitlow"></span>
    <p class="signer">Dana Whitlow<br>President</p>
  </article>

  <div class="faint-name" aria-hidden="true">KAJU</div>
  <p class="hashtag"><span>#</span>ALLKAJU</p>
</section>

<!-- Business card: back -->
<section class="card card-back">
  <div class="brand"><span class="brand-dot"></span>KAJU</div>
  <span class="divider"></span>
  <p class="tagline">Transportation<br>and Energy Services</p>
  <p class="website">www.<span>kajufreightco</span>.example</p>
</section>

<!-- Business card: front -->
<section class="card card-front">
  <svg class="shapes" viewBox="0 0 466 266" preserveAspectRatio="none" aria-hidden="true">
    <path fill="var(--teal)" d="M0 0H466V14C400 4 300 20 200 55C140 76 90 85 0 78Z"/>
    <path fill="var(--green)" d="M0 78C90 85 140 76 200 55C300 20 400 4 466 14V42C400 20 300 35 200 68C140 88 90 92 0 84Z"/>
    <path fill="var(--green)" d="M200 266C320 240 410 200 466 150V160C420 200 340 240 250 266Z"/>
    <path fill="var(--teal)" d="M250 266C340 240 420 200 466 160V266Z"/>
  </svg>

  <div class="brand"><span class="brand-dot"></span>KAJU</div>

  <div class="holder">
    <p class="name">DANA WHITLOW</p>
    <p class="title">President</p>
  </div>

  <address class="card-details" style="font-style:normal">
    <div class="company">KAJU Freightways &amp; Energy Services, Inc.</div>
    <div>4410 North Cactus Ridge Road</div>
    <div>Phoenix, AZ 85016</div>
    <div class="contacts">
      <div class="contact-line">
        <svg class="icon" viewBox="0 0 10 10"><path fill="var(--green)" d="M2 0.5L3.6 2.6 2.8 3.8C3.4 5 4.8 6.5 6.2 7.2L7.4 6.4 9.5 8 8.4 9.6C4.5 9.3 0.8 5.5 0.4 1.6Z"/></svg>602-555-0148
      </div>
      <div class="contact-line">
        <svg class="icon" viewBox="0 0 10 10"><rect x="0.6" y="1.8" width="8.8" height="6.4" fill="none" stroke="var(--green)" stroke-width="1"/><path d="M0.8 2l4.2 3.4L9.2 2" fill="none" stroke="var(--green)" stroke-width="1"/></svg>dana@kajufreightco.example
      </div>
      <div class="contact-line">
        <svg class="icon" viewBox="0 0 10 10"><circle cx="5" cy="5" r="4.3" fill="none" stroke="var(--green)" stroke-width="0.9"/><ellipse cx="5" cy="5" rx="1.8" ry="4.3" fill="none" stroke="var(--green)" stroke-width="0.8"/><path d="M0.8 5h8.4" stroke="var(--green)" stroke-width="0.7"/></svg>www.<span class="green">kajufreightco</span>.example
      </div>
    </div>
  </address>

  <div class="faint-name" aria-hidden="true">KAJU</div>
  <p class="hashtag"><span>#</span>ALLKAJU</p>
</section>

</body>
</html>
```